A resume/portfolio website for myself

I'm an independent software contractor, architect, tech trainer. I need a web site to present myself. Many ready to use portfolio designs are too artistic and focused on presenting design skills of the person. I like a nice website but the content should be a little less graphic than if you would present a graphic designer. Content could be presentation of me, core skill qualities and services and resume. Potentially a page with my tech courses in the longer run

```html
<!DOCTYPE html>
<html lang="en">
<head>
<meta charset="utf-8">
<title>Daniel Hartwell — Software Contractor, Architect, Tech Trainer</title>
<link rel="stylesheet" href="https://fonts.googleapis.com/css2?family=Montserrat:wght@500;600;700;800&family=Open+Sans:wght@400;600&display=swap">
<style>
:root{
  --orange:#e8581c;
  --ink:#1a1a1a;
  --dark:#141414;
  --dark-card:#222222;
  --grey-band:#e6e6e6;
  --grey-light:#f1f1f1;
  --bar-rest:#c6c6c6;
  --text:#444444;
  --muted:#8a8a8a;
  --white:#ffffff;
}
*{box-sizing:border-box;margin:0;padding:0}
html,body{width:1200px;height:4835px;overflow:hidden}
body{font-family:"Open Sans",Arial,sans-serif;color:var(--text);background:var(--white);position:relative}
.section{position:absolute;left:0;width:1200px}
.h-title{font-family:"Montserrat",Arial,sans-serif;font-weight:700;font-size:28px;letter-spacing:1px;text-align:center;text-transform:uppercase;position:absolute;left:0;width:1200px}
.intro{position:absolute;left:310px;width:580px;text-align:center;font-size:11px;line-height:20px;color:#555}

/* nav */
.nav{top:0;height:79px;background:var(--white)}
.brand{position:absolute;left:36px;top:22px;font-family:"Montserrat",sans-serif;font-weight:600;font-size:26px;color:var(--ink)}
.menu{position:absolute;left:383px;top:31px;display:flex;gap:34px;font-family:"Montserrat",sans-serif;font-size:11px;letter-spacing:.8px;color:#777;text-transform:uppercase}
.menu .active{color:var(--orange)}
.btn-resume{position:absolute;left:946px;top:21px;width:224px;height:37px;background:var(--orange);color:var(--white);font-family:"Montserrat",sans-serif;font-weight:700;font-size:12.5px;letter-spacing:.8px;display:flex;align-items:center;justify-content:center}

/* hero */
.hero{top:79px;height:575px;background:linear-gradient(90deg,#3a3a3a 0%,#5c5c5c 40%,#9a9a9a 70%,#c9c9c9 100%)}
.hero-name{position:absolute;left:171px;top:167px;font-family:"Montserrat",sans-serif;font-weight:700;font-size:48px;letter-spacing:2px;color:var(--white)}
.hero-text{position:absolute;left:171px;top:234px;width:460px;font-size:16.5px;line-height:24px;color:#e6e6e6}
.hero-sign{position:absolute;left:178px;top:349px;width:300px;height:58px;background:linear-gradient(90deg,rgba(255,255,255,.18),rgba(255,255,255,.05))}

/* experience */
.experience{top:654px;height:661px;background:var(--dark);color:var(--white)}
.experience .h-title{top:56px;color:var(--white)}
.timeline-line{position:absolute;left:599px;top:160px;width:2px;height:436px;background:#3c3c3c}
.timeline-end{position:absolute;left:590px;top:586px;width:20px;height:20px;border-radius:50%;background:#555}
.tl-icon{position:absolute;left:574px;width:52px;height:52px;border-radius:50%;border:2px solid #4a4a4a;background:#1c1c1c;display:flex;align-items:center;justify-content:center}
.tl-label{position:absolute;height:32px;background:#262626;color:var(--white);font-family:"Montserrat",sans-serif;font-weight:700;font-size:14.5px;display:flex;align-items:center;padding:0 18px}
.tl-label.left{right:633px}
.tl-label.left::after{content:"";position:absolute;right:-14px;top:0;border-left:14px solid #262626;border-top:16px solid transparent;border-bottom:16px solid transparent}
.tl-label.right{left:633px}
.tl-label.right::before{content:"";position:absolute;left:-14px;top:0;border-right:14px solid #262626;border-top:16px solid transparent;border-bottom:16px solid transparent}
.tl-text{position:absolute;width:357px;font-size:10.5px;line-height:19px;color:#cfcfcf}
.tl-text.right{left:670px}
.tl-text.left{right:670px;text-align:right}

/* jobs */
.jobs{top:1315px;height:531px;background:var(--white);border-top:8px solid #eeeeee}
.jobs .h-title{top:62px;color:var(--ink)}
.jobs .h-title span{color:#8b8b8b}
.col-title{position:absolute;top:142px;font-family:"Montserrat",sans-serif;font-weight:700;font-size:18px;color:var(--ink)}
.job-line{position:absolute;width:1px;background:#d0d0d0}
.job-dot{position:absolute;width:12px;height:12px;border-radius:50%;border:1.5px solid #aaa;background:var(--white)}
.job-divider{position:absolute;height:1px;background:#d8d8d8}
.job-name{position:absolute;font-family:"Montserrat",sans-serif;font-weight:700;font-size:16px;line-height:19px;color:var(--ink)}
.job-text{position:absolute;width:215px;font-size:10.5px;line-height:19px;color:#444}

/* skills */
.skills{top:1846px;height:560px;background:var(--grey-band)}
.skills .h-title{top:52px;color:var(--ink)}
.skills .intro{top:110px}
.skill{position:absolute;width:381px}
.skill-name{font-family:"Montserrat",sans-serif;font-weight:600;font-size:12px;letter-spacing:.4px;color:var(--ink);height:19px}
.bar{position:relative;height:30px;width:361px;background:var(--bar-rest)}
.bar::after{content:"";position:absolute;right:-20px;top:0;border-left:20px solid var(--bar-rest);border-top:15px solid transparent;border-bottom:15px solid transparent}
.bar-fill{position:absolute;left:0;top:0;height:30px;background:var(--ink)}
.bar-value{position:absolute;right:18px;top:7px;font-family:"Montserrat",sans-serif;font-weight:600;font-size:12px;color:#333}

/* professional skills */
.pro{top:2406px;height:471px;background:#111111}
.pro .h-title{top:70px;color:var(--white)}
.card{position:absolute;top:142px;width:272px;height:233px;background:var(--dark-card);text-align:center}
.card svg{position:absolute;left:106px;top:34px}
.card-title{position:absolute;top:134px;width:100%;font-family:"Montserrat",sans-serif;font-weight:700;font-size:14px;letter-spacing:1px;color:var(--white)}
.card-text{position:absolute;top:162px;width:100%;font-size:13.5px;line-height:20px;color:#8e8e8e}

/* portfolio */
.portfolio{top:2877px;height:757px;background:var(--white)}
.portfolio .h-title{top:56px;color:var(--ink)}
.portfolio .intro{top:120px}
.shot{position:absolute;width:278px;height:226px}

/* team */
.team{top:3634px;height:494px;background:linear-gradient(180deg,#8e8a84 0%,#b7b0a6 35%,#5a4e4a 75%,#2f2d33 100%)}

/* contact */
.contact{top:4128px;height:567px;background:var(--grey-light)}
.notch{position:absolute;left:568px;top:-1px;border-left:32px solid transparent;border-right:32px solid transparent;border-top:24px solid #36333a}
.contact .h-title{top:66px;color:var(--ink)}
.contact .intro{top:133px}
.info{position:absolute;left:267px;width:250px}
.info-head{display:flex;align-items:center;gap:9px;font-size:16px;color:#222}
.info-body{margin-top:8px;font-size:11px;line-height:22px;color:#555}
.field{position:absolute;left:545px;width:408px;height:33px;background:var(--white);border:1px solid #dedede;font-size:10.5px;color:#888;padding:9px 8px}
.submit{position:absolute;left:545px;top:4460px;top:460px;width:131px;height:34px;background:var(--orange);color:var(--white);font-family:"Montserrat",sans-serif;font-weight:700;font-size:10.5px;letter-spacing:.6px;display:flex;align-items:center;justify-content:center}

/* footer */
.footer{top:4695px;height:140px;background:#141414}
.social{position:absolute;left:0;width:1200px;top:30px;display:flex;justify-content:center;gap:26px}
.social span{width:20px;height:20px;border-radius:50%;background:var(--white)}
.copyright{position:absolute;left:0;width:1200px;top:84px;text-align:center;font-size:12.5px;color:#dcdcdc}
</style>
</head>
<body>

<header class="section nav">
  <div class="brand">Daniel Hartwell</div>
  <nav class="menu">
    <span class="active">Home</span><span>Skills</span><span>Experience</span><span>Portfolio</span><span>Education</span><span>Contact</span>
  </nav>
  <div class="btn-resume">DOWNLOAD MY RESUME</div>
</header>

<section class="section hero" role="img" aria-label="Black and white portrait of Daniel Hartwell on the right side of the banner">
  <h1 class="hero-name">DANIEL HARTWELL</h1>
  <p class="hero-text">Sed ut perspiciatis unde omnis iste natus error sit volu ptatem accusa ntium doloremque laudantium, totam rem aperiam, eaque ipsa quae illo inventore veritatis et quasi architecto beatae vitae dicta sunt</p>
  <div class="hero-sign" role="img" aria-label="Handwritten signature of Daniel Hartwell"></div>
</section>

<section class="section experience">
  <h2 class="h-title">Experience</h2>
  <div class="timeline-line"></div>
  <div class="timeline-end"></div>

  <div class="tl-icon" style="top:143px"><svg width="20" height="20" viewBox="0 0 20 20" fill="none" stroke="#8a8a8a" stroke-width="1.5"><rect x="3" y="2" width="14" height="16"/><line x1="6" y1="6" x2="14" y2="6"/><line x1="6" y1="10" x2="8" y2="10"/><line x1="11" y1="10" x2="14" y2="10"/><line x1="6" y1="14" x2="8" y2="14"/><line x1="11" y1="14" x2="14" y2="14"/></svg></div>
  <div class="tl-label left" style="top:153px">Neueorrisuam</div>
  <p class="tl-text right" style="top:142px">Sed ut perspiciatis unde omnis iste natus error sit voluptatem accusa ntiumdolor emque laudantium, totam reed ut perspiciatis unde omnis iste nats error sit voluptatem accusa</p>

  <div class="tl-icon" style="top:231px"><svg width="20" height="20" viewBox="0 0 20 20" fill="#8a8a8a"><rect x="4" y="7" width="12" height="10" rx="2"/><circle cx="7" cy="5" r="2.5"/><circle cx="13" cy="5" r="2.5"/></svg></div>
  <div class="tl-label right" style="top:241px">Neueorrisuam</div>
  <p class="tl-text left" style="top:230px">Sed ut perspiciatis unde omnis iste ntus error sit voluptatem accusa ntiumdolor emque laudantium, totam reed ut perspiciatis unde omnis iste nats error sit voluptatem accusa</p>

  <div class="tl-icon" style="top:320px"><svg width="20" height="20" viewBox="0 0 20 20" fill="#8a8a8a"><path d="M2 10 L18 3 L13 18 L10 12 Z"/></svg></div>
  <div class="tl-label left" style="top:330px">Neueorro uisuam</div>
  <p class="tl-text right" style="top:319px">Sed ut perspiciatis unde omnis iste natus error sit voluptatem accusa ntiumdolor emque laudantium, totam reed ut perspiciatis unde omnis iste nats error sit voluptatem accusa</p>

  <div class="tl-icon" style="top:408px"><svg width="20" height="20" viewBox="0 0 20 20" fill="#8a8a8a"><path d="M3 17 C3 8 9 3 17 3 C17 11 12 16 3 17 Z"/></svg></div>
  <div class="tl-label right" style="top:418px">Neueorris loremuam</div>
  <p class="tl-text left" style="top:407px">Sed ut perspiciatis unde omnis iste ntus error sit voluptatem accusa ntiumdolor emque laudantium, totam reed ut perspiciatis unde omnis iste nats error sit voluptatem accusa</p>

  <div class="tl-icon" style="top:494px"><svg width="20" height="20" viewBox="0 0 20 20" fill="none" stroke="#8a8a8a" stroke-width="1.5"><polyline points="2,17 2,3"/><polyline points="2,17 18,17"/><polyline points="4,14 8,9 11,12 17,5"/></svg></div>
  <div class="tl-label left" style="top:504px">Lorem euerisuam</div>
  <p class="tl-text right" style="top:493px">Sed ut perspiciatis unde omnis iste natus error sit voluptatem accusa ntiumdolor emque laudantium, totam reed ut perspiciatis unde omnis iste nats error sit voluptatem accusa</p>
</section>

<section class="section jobs">
  <h2 class="h-title">DANIEL HARTWELL <span>JOBS</span></h2>

  <h3 class="col-title" style="left:173px">ACTUAL JOBS</h3>
  <div class="job-line" style="left:323px;top:191px;height:269px"></div>
  <div class="job-divider" style="left:173px;top:275px;width:150px"></div>
  <div class="job-name" style="left:175px;top:201px">Neque porro<br>quisquam est</div>
  <div class="job-dot" style="left:317px;top:215px"></div>
  <p class="job-text" style="left:353px;top:193px">Sed ut perspiciatis unde omnis iste naus error sit voluptatem accusa ntiumdolor emque laudantium, totam rem.</p>
  <div class="job-name" style="left:175px;top:291px">Neque porro<br>quisquam est</div>
  <div class="job-dot" style="left:317px;top:305px"></div>
  <p class="job-text" style="left:353px;top:280px">Sed ut perspiciatis unde omnis iste ntus error sit voluptatem accusa ntiumdolor emque laudantium, totam rem</p>
  <p class="job-text" style="left:353px;top:355px">Sed ut perspiciatis unde omnis iste nats error sit voluptatem accusa ntiumdolor emque laudantium, totam rem.ed upers piciatis unde omnis iste natus error sit voluptatem accusa ntiumdolor</p>

  <h3 class="col-title" style="left:631px">FINISHED JOBS</h3>
  <div class="job-line" style="left:781px;top:191px;height:269px"></div>
  <div class="job-divider" style="left:631px;top:275px;width:150px"></div>
  <div class="job-name" style="left:633px;top:201px">Nequeorro<br>quisuam est</div>
  <div class="job-dot" style="left:775px;top:222px"></div>
  <p class="job-text" style="left:813px;top:193px">Sed ut perspiciatis unde omnis iste natus error sit voluptatem accusa ntiumdolor emque laudantium, totam rem.</p>
  <div class="job-name" style="left:633px;top:291px">Nequporro<br>quisuam</div>
  <div class="job-dot" style="left:775px;top:311px"></div>
  <p class="job-text" style="left:813px;top:280px">Sed ut perspiciatis unde omnis iste natus error sit voluptatem accusa ntiumdolor emque laudantium, totam rem.</p>
  <div class="job-divider" style="left:631px;top:365px;width:150px"></div>
  <div class="job-name" style="left:633px;top:388px">Nequporro<br>quisuam</div>
  <div class="job-dot" style="left:775px;top:408px"></div>
  <p class="job-text" style="left:813px;top:378px">Sed ut perspiciatis unde omnis iste natus error sit voluptatem accusa ntiumdolor emque laudantium, totam rem.</p>
</section>

<section class="section skills">
  <h2 class="h-title">Skills</h2>
  <p class="intro">Sed ut perspiciatis unde omnis iste ntus error sit voluptatem accusa ntiumdolor emque laudantium, totam remd ut perspiciatis unde omnis iste nats error sit voluptatem accusa ntiumdolor emque lauda</p>

  <div class="skill" style="left:175px;top:188px"><div class="skill-name">NEQUE PORRO QUISQUAM</div><div class="bar"><div class="bar-fill" style="width:75%"></div><span class="bar-value">80%</span></div></div>
  <div class="skill" style="left:175px;top:256px"><div class="skill-name">NEQUE PORRO QUISQUAM</div><div class="bar"><div class="bar-fill" style="width:58%"></div><span class="bar-value">40%</span></div></div>
  <div class="skill" style="left:175px;top:326px"><div class="skill-name">NEQUE PORRO QUISQUAM</div><div class="bar"><div class="bar-fill" style="width:88%"></div><span class="bar-value">90%</span></div></div>
  <div class="skill" style="left:175px;top:394px"><div class="skill-name">NEQUE QUISQUAM</div><div class="bar"><div class="bar-fill" style="width:64%"></div><span class="bar-value">70%</span></div></div>

  <div class="skill" style="left:644px;top:188px"><div class="skill-name">PORRO QUISQUAM</div><div class="bar"><div class="bar-fill" style="width:64%"></div><span class="bar-value">70%</span></div></div>
  <div class="skill" style="left:644px;top:256px"><div class="skill-name">NEQUE PO QUISQUAM</div><div class="bar"><div class="bar-fill" style="width:79%"></div><span class="bar-value">80%</span></div></div>
  <div class="skill" style="left:644px;top:326px"><div class="skill-name">NEQUE PORRO QUISQUAM</div><div class="bar"><div class="bar-fill" style="width:79%"></div><span class="bar-value">80%</span></div></div>
  <div class="skill" style="left:644px;top:394px"><div class="skill-name">PORRO QUISQUAM</div><div class="bar"><div class="bar-fill" style="width:39%"></div><span class="bar-value">30%</span></div></div>
</section>

<section class="section pro">
  <h2 class="h-title">Professional Skills</h2>
  <div class="card" style="left:176px">
    <svg width="60" height="60" viewBox="0 0 60 60" fill="none" stroke="#fff" stroke-width="2"><rect x="6" y="8" width="48" height="34" rx="2"/><line x1="24" y1="42" x2="22" y2="52"/><line x1="36" y1="42" x2="38" y2="52"/><line x1="18" y1="52" x2="42" y2="52"/><circle cx="24" cy="25" r="8"/><path d="M24 17 V25 H32"/><line x1="36" y1="18" x2="48" y2="18"/><line x1="36" y1="25" x2="48" y2="25"/><line x1="36" y1="32" x2="44" y2="32"/></svg>
    <div class="card-title">SOFTWARE CONTRACTOR</div>
    <div class="card-text">Lorem ipsum dolor sit amet,<br>consectetur adipiscinelit</div>
  </div>
  <div class="card" style="left:469px">
    <svg width="60" height="60" viewBox="0 0 60 60" fill="none" stroke="#fff" stroke-width="2"><path d="M10 8 L18 16 L14 20 L6 12 Z"/><line x1="16" y1="18" x2="48" y2="50"/><rect x="44" y="46" width="8" height="8" transform="rotate(45 48 50)"/><path d="M50 6 A10 10 0 0 0 38 20 L12 46 A4 4 0 0 0 18 52 L44 26 A10 10 0 0 0 56 14 L50 18 L44 16 L42 10 Z"/></svg>
    <div class="card-title">ARCHITECT</div>
    <div class="card-text">Lorem ipsum dolor sit amet,<br>consectetur adipiscinelit</div>
  </div>
  <div class="card" style="left:761px">
    <svg width="60" height="60" viewBox="0 0 60 60" fill="none" stroke="#fff" stroke-width="2"><rect x="8" y="4" width="18" height="10" rx="2"/><circle cx="18" cy="22" r="6"/><path d="M6 56 V40 A12 12 0 0 1 30 40 V56"/><circle cx="42" cy="24" r="6"/><path d="M30 56 V42 A12 12 0 0 1 54 42 V56"/><line x1="12" y1="46" x2="12" y2="56"/><line x1="48" y1="46" x2="48" y2="56"/></svg>
    <div class="card-title">TECH TRAINER</div>
    <div class="card-text">Lorem ipsum dolor sit amet,<br>consectetur adipiscinelit</div>
  </div>
</section>

<section class="section portfolio">
  <h2 class="h-title">Portfolio</h2>
  <p class="intro">Sed ut perspiciatis unde omnis iste ntus error sit voluptatem accusa ntiumdolor emque laudantium, totam remd ut perspiciatis unde omnis iste nats error sit voluptatem accusa ntiumdolor emque lauda</p>
  <div class="shot" style="left:173px;top:190px;background:linear-gradient(135deg,#5b534c,#c9c6c2 60%,#6f5a48)" role="img" aria-label="Colleagues reviewing printed charts at a desk with a laptop and coffee"></div>
  <div class="shot" style="left:462px;top:190px;background:linear-gradient(135deg,#1f2f4a,#5a7aa6 55%,#c7d6e6)" role="img" aria-label="Hand touching a glowing blue data chart"></div>
  <div class="shot" style="left:749px;top:190px;background:linear-gradient(135deg,#d8d6d4,#b5aea8 55%,#7a6e66)" role="img" aria-label="Person sketching beside a laptop on a bright desk"></div>
  <div class="shot" style="left:173px;top:426px;background:linear-gradient(135deg,#2c3a52,#7d8aa0 55%,#c9c3bb)" role="img" aria-label="Business people in suits pointing at a tablet"></div>
  <div class="shot" style="left:462px;top:426px;background:linear-gradient(135deg,#e9dccb,#a89a8c 55%,#4c4a4c)" role="img" aria-label="Hands typing on a laptop keyboard"></div>
  <div class="shot" style="left:749px;top:426px;background:linear-gradient(135deg,#e6eef4,#9aa8b4 50%,#3e4650)" role="img" aria-label="Two colleagues working together at a computer screen"></div>
</section>

<section class="section team" role="img" aria-label="Group photo of a training class standing together in an office"></section>

<section class="section contact">
  <div class="notch"></div>
  <h2 class="h-title">Contact</h2>
  <p class="intro">Sed ut perspiciatis unde omnis iste ntus error sit voluptatem accusa ntiumdolor emque laudantium, totam remd ut perspiciatis unde omnis iste nats error sit voluptatem accusa ntiumdolor emque lauda</p>

  <div class="info" style="top:206px">
    <div class="info-head"><svg width="18" height="20" viewBox="0 0 18 20" fill="none" stroke="#333" stroke-width="1.4"><path d="M9 19 C4 13 2 10 2 7 A7 7 0 0 1 16 7 C16 10 14 13 9 19 Z"/><circle cx="9" cy="7" r="2.5"/></svg>Address</div>
    <div class="info-body">Norvik Consult BV<br>Lorem ipsmh Lore dummy<br>Dummy location 8758 dumm<br>ZZ99 1AB dummy citt</div>
  </div>
  <div class="info" style="top:346px">
    <div class="info-head"><svg width="20" height="16" viewBox="0 0 20 16" fill="none" stroke="#333" stroke-width="1.4"><rect x="1" y="2" width="18" height="12"/><polyline points="1,2 10,9 19,2"/></svg>Email</div>
    <div class="info-body" style="margin-top:2px">hello@hartwell-tech.dev</div>
  </div>
  <div class="info" style="top:416px">
    <div class="info-head"><svg width="18" height="18" viewBox="0 0 18 18" fill="none" stroke="#333" stroke-width="1.4"><path d="M4 1 L7 5 L5 7 C6 10 8 12 11 13 L13 11 L17 14 L15 17 C8 16 2 10 1 3 Z"/></svg>Phone</div>
    <div class="info-body" style="margin-top:2px">01632 960214, 01632 960215</div>
  </div>

  <div class="field" style="top:208px">Name:</div>
  <div class="field" style="top:249px">Email:</div>
  <div class="field" style="top:289px">Phone:</div>
  <div class="field" style="top:329px;height:135px">Message:</div>
  <div class="submit" style="top:474px">SUBMIT HERE</div>
</section>

<footer class="section footer">
  <div class="social" aria-label="Social profiles"><span></span><span></span><span></span><span></span></div>
  <p class="copyright">© 2020 Daniel Hartwell. All Rights Are Reserved.Terms of Use | Privacy Policy</p>
</footer>

</body>
</html>
```